Corvelle Meadow Organic Flower Farm, Farmer Florist

I am a flower grower and florist, so I do everything from the field to the vase. I want to include my website, phone, email and instagram

```html
<!DOCTYPE html>
<html lang="en">
<head>
<meta charset="utf-8">
<title>Corvelle Meadow – Business Card</title>
<link href="https://fonts.googleapis.com/css2?family=Cinzel:wght@400;600&family=Arimo&family=Cormorant+Garamond:ital,wght@0,600;1,500&display=swap" rel="stylesheet">
<style>
  :root{
    --backdrop:#e4e4e4;
    --bark:#634e39;
    --bark-ink:#5f4a36;
    --wheat:#d6a764;
    --paper:#ffffff;
    --rule:#b9b9b9;
  }
  *{margin:0;padding:0;box-sizing:border-box}
  html,body{width:1093px;height:1200px;overflow:hidden;background:var(--backdrop)}
  .canvas{position:relative;width:1093px;height:1200px}
  .card{position:absolute;left:264px;width:580px;height:357px;box-shadow:0 2px 6px rgba(0,0,0,.25)}
  .card--contact{top:226px;background:var(--bark);color:var(--wheat);text-align:center}
  .card--brand{top:620px;background:var(--paper);text-align:center}

  .person__name{position:absolute;top:78px;left:0;right:0;font-family:'Cinzel',serif;font-weight:600;font-size:31px;letter-spacing:.5px;line-height:1}
  .person__role{position:absolute;top:112px;left:0;right:0;font-family:'Arimo',sans-serif;font-size:21px;line-height:1}

  .icon-row{position:absolute;top:153px;left:0;right:0;display:flex;justify-content:center;align-items:center;gap:5px}
  .icon-row__rule{width:64px;height:1px;background:var(--wheat);opacity:.7;margin:0 7px}
  .icon-tile{width:31px;height:31px;border-radius:3px;background:var(--wheat);display:flex;align-items:center;justify-content:center}
  .icon-tile svg{width:21px;height:21px}

  .contact-list{position:absolute;top:200px;left:0;right:0;list-style:none;font-family:'Arimo',sans-serif;font-size:21px;line-height:27px}

  .brand__name{position:absolute;top:158px;left:0;right:0;font-family:'Cinzel',serif;font-weight:400;font-size:44px;letter-spacing:5px;color:var(--bark-ink);line-height:1}
  .brand__tagline{position:absolute;top:212px;left:0;right:0;font-family:'Cormorant Garamond',serif;font-style:italic;font-weight:500;font-size:22px;letter-spacing:1px;color:var(--wheat);line-height:1}
  .brand__est{position:absolute;top:243px;left:0;right:0;font-family:'Cormorant Garamond',serif;font-weight:600;font-size:14px;letter-spacing:6px;color:var(--bark-ink);line-height:1}

  .social-row{position:absolute;top:288px;left:0;right:0;display:flex;justify-content:center;align-items:center}
  .social-row__rule{height:1px;background:var(--rule)}
  .social-row__rule--left{width:75px;margin-right:7px}
  .social-row__rule--right{width:78px;margin-left:7px}
  .social-dot{width:37px;height:37px;border-radius:50%;background:var(--wheat)}
</style>
</head>
<body>
<main class="canvas">
  <section class="card card--contact">
    <h1 class="person__name">Elena Marsh</h1>
    <p class="person__role">Managing Director</p>
    <div class="icon-row">
      <span class="icon-row__rule"></span>
      <span class="icon-tile" aria-label="Phone">
        <svg viewBox="0 0 24 24"><path fill="var(--bark)" d="M3 9c0-3 4-4 9-4s9 1 9 4v2h-4V9.5c-1-.6-3-.9-5-.9s-4 .3-5 .9V11H3zM7 12l2-3h6l2 3v6H7z"/><g fill="var(--wheat)"><rect x="9" y="12" width="1.5" height="1.5"/><rect x="11.25" y="12" width="1.5" height="1.5"/><rect x="13.5" y="12" width="1.5" height="1.5"/><rect x="9" y="14.5" width="1.5" height="1.5"/><rect x="11.25" y="14.5" width="1.5" height="1.5"/><rect x="13.5" y="14.5" width="1.5" height="1.5"/></g></svg>
      </span>
      <span class="icon-tile" aria-label="Email">
        <svg viewBox="0 0 24 24"><rect x="3" y="6" width="18" height="12" fill="none" stroke="var(--bark)" stroke-width="1.6"/><path d="M3 6l9 7 9-7M3 18l7-6M21 18l-7-6" fill="none" stroke="var(--bark)" stroke-width="1.4"/></svg>
      </span>
      <span class="icon-tile" aria-label="Website">
        <svg viewBox="0 0 24 24"><circle cx="12" cy="12" r="9" fill="var(--bark)"/><path d="M8 7c2 0 3 1 2.5 3s-2.5 1.5-2.5 4 1.5 3 1 4M15 6c-1 2 1 3 2.5 3M14 13c2 0 3 1 2 4" fill="none" stroke="var(--wheat)" stroke-width="1.6"/></svg>
      </span>
      <span class="icon-row__rule"></span>
    </div>
    <ul class="contact-list">
      <li>044-987 650 312</li>
      <li>hello@corvellemeadow.com</li>
      <li>www.corvellemeadow.com</li>
    </ul>
  </section>

  <section class="card card--brand">
    <h2 class="brand__name">CORVELLE</h2>
    <p class="brand__tagline">organic flower farm</p>
    <p class="brand__est">EST. 2019</p>
    <div class="social-row">
      <span class="social-row__rule social-row__rule--left"></span>
      <span class="social-dot" aria-label="Social profile"></span>
      <span class="social-row__rule social-row__rule--right"></span>
    </div>
  </section>
</main>
</body>
</html>
```